Company or website name
- The Steadfast Haulers and Storage
- Links to the website
- Pinecrestcartage.com
- Describe your company and organization and target audience
- Residential and commercial moving and relocation service that needs a website redesign.
- The design should have the following
- I NEED THE WEBSITE TO BE SIMPLE AND STRAIGHT TO THE POINT...MAIN CONCERN IS THAT THEY FILL OUT INFORMATION TO GET QUOTE. SITE EXAMPLE THAT I LIKE IS ( WWW.MYDORVALS.COM) https://www.corvellfreight.com/

```html
<!DOCTYPE html>
<html lang="en">
<head>
<meta charset="utf-8">
<title>The Steadfast Haulers and Storage</title>
<link href="https://fonts.googleapis.com/css2?family=Montserrat:wght@400;600;700;800&family=Open+Sans:ital,wght@0,400;0,600;1,400;1,600&display=swap" rel="stylesheet">
<style>
:root{
  --orange:#f05a1e;
  --orange-dark:#d94a12;
  --ink:#2b2b2b;
  --dark:#2e2e2e;
  --dark-2:#3a3a3a;
  --text:#5b5b5b;
  --muted:#9a9a9a;
  --light:#f3f3f3;
  --line:#e2e2e2;
  --white:#ffffff;
  --green:#4caf50;
}
*{box-sizing:border-box;margin:0;padding:0}
html,body{width:1200px;height:2804px;overflow:hidden}
body{font-family:"Open Sans",Arial,sans-serif;color:var(--text);background:var(--white);position:relative}
h1,h2,h3,h4,.brand,.site-nav a,.btn{font-family:"Montserrat",Arial,sans-serif}
section,header,footer{position:absolute;left:0;width:1200px}

/* ---------- Hero ---------- */
.hero{top:0;height:620px;background:var(--white)}
.hero-band{position:absolute;left:0;top:0;width:450px;height:620px;background:var(--orange)}
.brand{position:absolute;left:40px;top:18px;display:flex;align-items:center;gap:10px;color:var(--white);font-weight:800;font-size:26px;letter-spacing:2px}
.brand-dot{width:22px;height:22px;border-radius:50%;background:var(--white)}
.site-nav{position:absolute;left:510px;top:26px;display:flex;gap:20px}
.site-nav a{font-size:9.5px;font-weight:600;letter-spacing:.5px;color:var(--ink);text-decoration:none;text-transform:uppercase;white-space:nowrap}
.site-nav a.active{color:var(--orange)}
.hero-photo{position:absolute;left:240px;top:80px;width:640px;height:440px;background:linear-gradient(180deg,#b9cbe0 0%,#d9e2ea 45%,#c7c9c6 70%,#8c8f8a 100%)}
.hero-caption{position:absolute;left:240px;top:418px;width:585px;text-align:center;color:var(--white)}
.hero-caption h1{font-size:26px;font-weight:700;text-shadow:0 1px 3px rgba(0,0,0,.35)}
.hero-caption p{font-size:11px;margin-top:6px}
.hero-call{position:absolute;left:40px;top:520px;color:var(--white)}
.hero-call em{font-size:15px;font-weight:600}
.hero-call strong{display:block;font-family:"Montserrat",Arial,sans-serif;font-size:40px;font-weight:700;margin-top:2px}

.quote-card{position:absolute;left:825px;top:105px;width:355px;height:445px;background:var(--white);box-shadow:0 6px 24px rgba(0,0,0,.18)}
.quote-head{background:var(--orange);color:var(--white);padding:18px 24px 14px}
.quote-head h2{font-size:26px;font-weight:800;line-height:1.05}
.quote-head h2 span{font-style:italic}
.quote-tabs{display:flex;border-bottom:1px solid var(--line)}
.quote-tab{flex:1;height:46px;display:flex;align-items:center;justify-content:center;border-right:1px solid var(--line)}
.quote-tab:last-child{border-right:0}
.quote-tab.active{background:var(--orange)}
.quote-form{padding:14px 20px}
.field-row{display:flex;gap:10px;margin-bottom:10px}
.field{flex:1;height:30px;border:1px solid var(--line);background:var(--light);font-size:10px;color:var(--muted);padding:8px 10px}
.quote-actions{display:flex;gap:10px;margin-top:14px}
.btn{flex:1;height:34px;display:flex;align-items:center;justify-content:center;font-size:11px;font-weight:700;color:var(--white)}
.btn-quote{background:var(--green)}
.btn-book{background:var(--dark)}

/* ---------- About ---------- */
.about{top:620px;height:470px}
.about-text{position:absolute;left:170px;top:100px;width:410px}
.about-text h2{font-size:24px;font-weight:700;color:var(--orange);line-height:1.25;white-space:nowrap}
.about-text p{font-size:11.5px;line-height:1.7;margin-top:14px}
.about-photo{position:absolute;left:610px;top:80px;width:390px;height:270px;background:linear-gradient(135deg,#e9dccb 0%,#c9a27a 55%,#a57d55 100%)}

/* ---------- Services ---------- */
.services{top:1090px;height:540px;background:var(--dark)}
.services h2{position:absolute;left:150px;top:60px;font-size:28px;font-weight:700;color:var(--orange)}
.services .lead{position:absolute;left:150px;top:104px;width:520px;font-size:12px;font-style:italic;color:#d0d0d0;line-height:1.5}
.service-grid{position:absolute;left:150px;top:160px;display:flex;gap:20px}
.service-card{width:215px;height:300px;background:var(--white)}
.service-photo{height:140px}
.service-card h3{font-size:14px;font-weight:700;color:var(--orange);padding:14px 14px 6px}
.service-card p{font-size:10.5px;line-height:1.55;padding:0 14px}
.service-card .more{display:inline-block;margin:12px 14px 0;background:var(--dark);color:var(--white);font-family:"Montserrat",Arial,sans-serif;font-size:10px;font-weight:600;padding:7px 14px}

/* ---------- Areas ---------- */
.areas{top:1630px;height:515px;background:var(--white)}
.areas-text{position:absolute;left:150px;top:70px;width:270px}
.areas-text h2{font-size:28px;font-weight:700;color:var(--orange)}
.areas-text .lead{font-size:12px;font-style:italic;font-weight:600;color:var(--ink);line-height:1.55;margin-top:12px}
.areas-text p{font-size:11px;line-height:1.7;margin-top:12px}
.areas-grid{position:absolute;left:650px;top:0;width:550px;height:515px;display:grid;grid-template-columns:repeat(3,1fr);grid-template-rows:repeat(3,1fr);gap:2px;background:#444}
.area-tile{background:var(--dark);display:flex;flex-direction:column;align-items:center;justify-content:center;gap:10px;color:var(--white);font-size:11px;font-family:"Montserrat",Arial,sans-serif}
.area-tile.accent{background:var(--orange)}
.area-photo{position:absolute;left:450px;top:0;width:200px;height:172px;background:linear-gradient(135deg,#f7a47f,#f05a1e)}

/* ---------- Testimonials ---------- */
.testimonials{top:2145px;height:285px}
.testi-band{position:absolute;left:0;top:0;width:470px;height:285px;background:var(--orange);overflow:hidden}
.testi-band h2{position:absolute;left:150px;top:110px;font-size:30px;font-weight:700;color:var(--white)}
.testi-band p{position:absolute;left:150px;top:152px;font-size:11px;font-style:italic;color:var(--white)}
.testi-mark{position:absolute;left:320px;top:40px;font-family:"Montserrat",Arial,sans-serif;font-size:140px;font-weight:800;color:rgba(255,255,255,.14);line-height:1}
.testi-avatar{position:absolute;left:555px;top:100px;width:72px;height:72px;border-radius:50%;background:linear-gradient(135deg,#d8d8d8,#9e9e9e)}
.testi-quote{position:absolute;left:650px;top:96px;width:400px}
.testi-quote p{font-size:11.5px;line-height:1.65}
.testi-quote cite{display:block;margin-top:10px;font-size:11px;font-weight:600;font-style:italic;color:var(--ink)}

/* ---------- Footer ---------- */
.site-footer{top:2480px;height:324px;background:var(--light)}
.foot-brand{position:absolute;left:150px;top:60px}
.foot-brand .brand{position:static;color:var(--ink);font-size:22px}
.foot-brand .brand-dot{background:var(--orange)}
.foot-brand p{font-size:9.5px;line-height:1.6;margin-top:14px;width:180px}
.foot-col{position:absolute;top:60px}
.foot-col h4{font-size:12px;font-weight:700;color:var(--ink);margin-bottom:10px}
.foot-col p,.foot-col li{font-size:10px;line-height:1.75;list-style:none}
.social li{display:flex;align-items:center;gap:8px}
.social span{width:12px;height:12px;background:var(--ink)}
.rating{position:absolute;left:985px;top:60px}
.stars{color:var(--orange);font-size:16px;letter-spacing:2px}
.rating p{font-size:9px;margin-top:4px}
.badges{display:flex;gap:8px;margin-top:12px}
.badge{width:44px;height:36px;background:#cfcfcf}
</style>
</head>
<body>

<header class="hero">
  <div class="hero-band"></div>
  <div class="brand"><span class="brand-dot"></span>STEADFAST</div>
  <nav class="site-nav">
    <a class="active" href="#">Home</a>
    <a href="#">About Us</a>
    <a href="#">Residential Moving</a>
    <a href="#">Services</a>
    <a href="#">Careers</a>
    <a href="#">Moving Resources</a>
    <a href="#">Other Moving Links</a>
  </nav>
  <div class="hero-photo" role="img" aria-label="Moving truck parked outside a suburban house"></div>
  <div class="hero-caption">
    <h1>We Help Move Lives Forward</h1>
    <p>Providing local, long distance and commercial moving services since 2008</p>
  </div>
  <div class="hero-call">
    <em>Call Today for Quote</em>
    <strong>(555) 284-1937</strong>
  </div>

  <div class="quote-card">
    <div class="quote-head">
      <h2>GET A <span>FREE</span><br>MOVING QUOTE!</h2>
    </div>
    <div class="quote-tabs">
      <div class="quote-tab active"><svg width="20" height="20" viewBox="0 0 20 20"><path d="M3 10 L10 3 L17 10 V17 H3 Z" fill="none" stroke="#fff" stroke-width="2"/></svg></div>
      <div class="quote-tab"><svg width="20" height="20" viewBox="0 0 20 20"><rect x="4" y="3" width="12" height="14" fill="none" stroke="#888" stroke-width="2"/></svg></div>
      <div class="quote-tab"><svg width="22" height="20" viewBox="0 0 22 20"><rect x="1" y="5" width="13" height="9" fill="none" stroke="#888" stroke-width="2"/><path d="M14 8 H18 L21 11 V14 H14" fill="none" stroke="#888" stroke-width="2"/></svg></div>
      <div class="quote-tab"><svg width="20" height="20" viewBox="0 0 20 20"><rect x="3" y="5" width="14" height="12" fill="none" stroke="#888" stroke-width="2"/><path d="M3 9 H17" stroke="#888" stroke-width="2"/></svg></div>
    </div>
    <form class="quote-form">
      <div class="field-row"><div class="field">First Name</div><div class="field">Last Name</div></div>
      <div class="field-row"><div class="field">Email Address</div><div class="field">Phone</div></div>
      <div class="field-row"><div class="field">Moving From (Zip)</div><div class="field">Moving To (Zip)</div></div>
      <div class="field-row"><div class="field">Move Date</div><div class="field">Size of Move</div></div>
      <div class="quote-actions">
        <div class="btn btn-quote">Free Quote</div>
        <div class="btn btn-book">Book A Reservation</div>
      </div>
    </form>
  </div>
</header>

<section class="about">
  <div class="about-text">
    <h2>Moving Families &amp; Businesses<br>For Over A Decade</h2>
    <p>As a local mover, our team has handled thousands of household and office relocations across the region. We treat every item with care, arrive on time and keep pricing clear from the first call.</p>
    <p>From single rooms to full estates, our trained crews pack, load, move and store your belongings safely. Ask about flexible dates, secure storage and fully insured service for peace of mind.</p>
  </div>
  <div class="about-photo" role="img" aria-label="Couple sitting among moving boxes in a new home"></div>
</section>

<section class="services">
  <h2>Moving Services</h2>
  <p class="lead">From neighbourhood moves to corporate relocations, our crews get you where you need to be.</p>
  <div class="service-grid">
    <article class="service-card">
      <div class="service-photo" role="img" aria-label="Movers carrying boxes into a home" style="background:linear-gradient(135deg,#c98a62,#7a4a30)"></div>
      <h3>Residential Moving</h3>
      <p>Careful packing and loading for apartments, condos and family homes of any size.</p>
      <span class="more">Read More</span>
    </article>
    <article class="service-card">
      <div class="service-photo" role="img" aria-label="Crew moving office furniture" style="background:linear-gradient(135deg,#d6a07a,#8d5a3b)"></div>
      <h3>Commercial Moving</h3>
      <p>Planned office moves that keep downtime low and your business running.</p>
      <span class="more">Read More</span>
    </article>
    <article class="service-card">
      <div class="service-photo" role="img" aria-label="Mover helping an older client with boxes" style="background:linear-gradient(135deg,#b77b5b,#5e3b2a)"></div>
      <h3>Senior Moving</h3>
      <p>Patient, respectful help for seniors moving to a new home or community.</p>
      <span class="more">Read More</span>
    </article>
    <article class="service-card">
      <div class="service-photo" role="img" aria-label="Row of storage unit doors" style="background:linear-gradient(135deg,#c8694a,#7e2f1c)"></div>
      <h3>Storage</h3>
      <p>Clean, secure short and long term storage for furniture and goods.</p>
      <span class="more">Read More</span>
    </article>
  </div>
</section>

<section class="areas">
  <div class="areas-text">
    <h2>Areas Served</h2>
    <p class="lead">Our extensive network of offices provides us with a broad range of capabilities to best serve our customers' unique moving and storage needs.</p>
    <p>We serve towns across the county and neighbouring states, with local crews who know the roads, the buildings and the rules. Call us to confirm service in your area and get a fast estimate for your move.</p>
  </div>
  <div class="area-photo" role="img" aria-label="Orange tinted photo of a moving crew"></div>
  <div class="areas-grid">
    <div class="area-tile accent"><svg width="34" height="34" viewBox="0 0 34 34"><rect x="8" y="5" width="18" height="25" fill="none" stroke="#fff" stroke-width="2"/><path d="M12 10h4M18 10h4M12 16h4M18 16h4M12 22h4M18 22h4" stroke="#fff" stroke-width="2"/></svg>Office</div>
    <div class="area-tile"><svg width="34" height="34" viewBox="0 0 34 34"><path d="M5 17 L17 6 L29 17 V29 H5 Z" fill="none" stroke="#fff" stroke-width="2"/></svg>Home</div>
    <div class="area-tile"><svg width="34" height="34" viewBox="0 0 34 34"><path d="M17 4 C11 4 8 8 8 13 C8 20 17 30 17 30 C17 30 26 20 26 13 C26 8 23 4 17 4 Z" fill="none" stroke="#fff" stroke-width="2"/><circle cx="17" cy="13" r="3" fill="#fff"/></svg>Regional</div>
    <div class="area-tile"><svg width="34" height="34" viewBox="0 0 34 34"><rect x="7" y="9" width="20" height="18" fill="none" stroke="#fff" stroke-width="2"/><path d="M7 14 H27" stroke="#fff" stroke-width="2"/></svg>Local</div>
    <div class="area-tile accent"><svg width="38" height="34" viewBox="0 0 38 34"><rect x="3" y="10" width="20" height="13" fill="none" stroke="#fff" stroke-width="2"/><path d="M23 14 H30 L35 19 V23 H23" fill="none" stroke="#fff" stroke-width="2"/><circle cx="10" cy="26" r="3" fill="#fff"/><circle cx="29" cy="26" r="3" fill="#fff"/></svg>Long Distance</div>
    <div class="area-tile"><svg width="34" height="34" viewBox="0 0 34 34"><path d="M5 12 L17 5 L29 12 L17 19 Z M5 12 V24 L17 31 L29 24 V12" fill="none" stroke="#fff" stroke-width="2"/></svg>Logistics</div>
    <div class="area-tile"><svg width="34" height="34" viewBox="0 0 34 34"><circle cx="17" cy="17" r="12" fill="none" stroke="#fff" stroke-width="2"/><path d="M5 17 H29 M17 5 V29" stroke="#fff" stroke-width="2"/></svg>International</div>
    <div class="area-tile accent"><svg width="34" height="34" viewBox="0 0 34 34"><rect x="6" y="8" width="22" height="20" fill="none" stroke="#fff" stroke-width="2"/><path d="M6 14 H28 M12 8 V4 M22 8 V4" stroke="#fff" stroke-width="2"/></svg>Short Term</div>
    <div class="area-tile"><svg width="34" height="34" viewBox="0 0 34 34"><rect x="6" y="6" width="22" height="22" fill="none" stroke="#fff" stroke-width="2"/><path d="M6 13 H28 M6 20 H28" stroke="#fff" stroke-width="2"/></svg>Storage</div>
  </div>
</section>

<section class="testimonials">
  <div class="testi-band">
    <div class="testi-mark">99</div>
    <h2>Testimonials</h2>
    <p>Our Customers Are Saying</p>
  </div>
  <div class="testi-avatar" role="img" aria-label="Customer portrait"></div>
  <blockquote class="testi-quote">
    <p>"The crew arrived early, wrapped every piece of furniture and had our whole house loaded before lunch. Friendly, careful and fairly priced. We would gladly book them again for our next move."</p>
    <cite>Marcus Delane, Fairfield, CT</cite>
  </blockquote>
</section>

<footer class="site-footer">
  <div class="foot-brand">
    <div class="brand"><span class="brand-dot"></span>STEADFAST</div>
    <p>© 2024 The Steadfast Haulers and Storage. All rights reserved.</p>
  </div>
  <div class="foot-col" style="left:420px">
    <h4>Headquarters</h4>
    <p>The Steadfast Haulers and Storage<br>418 Quarry Lane<br>Ridgefield, CT 06877<br>Toll Free: (555) 284-1937<br>Local: (555) 284-1938</p>
  </div>
  <div class="foot-col" style="left:640px">
    <h4>Moving Resources</h4>
    <ul><li>Moving Tips</li><li>Packing Guide</li><li>Moving Checklist</li></ul>
  </div>
  <div class="foot-col social" style="left:800px">
    <h4>Connect With Us</h4>
    <ul><li><span></span>Community Page</li><li><span></span>Updates</li><li><span></span>Photo Feed</li></ul>
  </div>
  <div class="rating">
    <div class="stars">★★★★★</div>
    <p>Rated 4.9 by our customers</p>
    <div class="badges"><div class="badge"></div><div class="badge"></div></div>
  </div>
</footer>

</body>
</html>
```